Lotstallmart.com Webpage Design

Design Brief for lotstallmart.com (Copy of Brief also in attached Word file)

Name of Website- lotstallmart.com (existing logo and look & feel of website to be changed)

Logo - Finalised. The logo files are attached with the brief as “logo.jpeg”. The “Blue- Grey” version of the logo is for use on lighter backgrounds and the “Orange-White” version of the logo is for use on darker backgrounds. (A full Black version of the logo is also attached). Both versions may be used in different parts of the website. All attached files are in .png format.
Status - The website in functional and is undergoing user trials. However, we want to improve the look & feel of the website so at it seems
a. cotemporary,
b. Easy to Navigate
c. professional and
d. Vibrant.

Please visit ‘lotstallmart.com’ to check out the website and its functionalities – please use it only as a reference for the features & functions to be provided, however the designer should use a ‘Free Hand’ in designing the composition of various parts of the webpage without getting too influenced by the existing design

Objective of the Website ‘lotstallmart.com –
a. It is a portal focussed on listing of ‘Retail’ specific real-estate properties by developers, owners and realty brokers. The properties shall listed under the following four categories-
i. Retail Malls
ii. Shopping Complexes
iii. High-street shops
iv. Retail Warehouses
*refer lotstallmart.com for better clarity

b. The abovementioned properties shall be listed either for ‘Sale’ or ‘rent\lease’ or both

c. Users shall visit the site in case they wish to acquire a retail \ shop space either on ‘sale’ or ‘rent’. These Users would be able to specify the ‘Search Criteria’ through the tool-bars provided on the website – the ‘Search Criteria’ shall comprise of ‘Type of space category’, ‘City’, ‘Locality’, transaction type ie ‘Rent \ Sale’ and ‘Area Range’

d. The main revenue model for the website shall be listing fee ( or advertising charges ) payable by those listing their properties on the website.

Three Main Pages of Website (lotstallmart.com) that need to be designed -
a. Main Home Page (visit the web link - http://lotstallmart.com/ ) - The main home page has the “Search Toolbar” for specifying of Search Criteria by the User. It shall also have the following features & functions-
i. Main Advertising Banner
ii. Featured Projects
iii. New Launches
iv. Toolbar with buttons – ‘Advertise with Us’, ‘Listings Alert’, ‘Mart Wizards’, ‘Advertiser Login’

b. Property Listings Page (visit the web link - http://lotstallmart.com/gurgaon-in-india ) - The List of property options that match the Criteria specified by the ‘User’ get displayed on this page.

c. Property Detail Page - When the ‘User’ clicks on the “More….” Button on the ‘Property Listings Page’ (given in point b. above) the web page with the details of the property opens. (For Example – visit the web link - http://lotstallmart.com/vorne-Shopping-Complex-vorne-quadrion-gurgaon-636 )

Note:- Please refer to attached ‘Shopping’ related images the designer may use them on the website to provide a look & feel of retail if required – either separately or rotate in a single window

Target Market(s)

Retailers & Investors looking for retail space, Real Estate Brokers, Developers

Industry/Entity Type

Advertising

Number of Pages Required

3 page

Requirements
Must have
• Refer to existing site lotstallmart.com -- all the existing functionalities are a must have.
Nice to have
• The Designer may use the retail related images on the website if required for making it more vibrant. Refer attached images Shopping(1-6).jpg

```html
<!DOCTYPE html>
<html lang="en">
<head>
<meta charset="utf-8">
<title>Lotstallmart.com – Home</title>
<link href="https://fonts.googleapis.com/css2?family=Ubuntu:wght@400;500;700&family=Open+Sans:wght@400;600&display=swap" rel="stylesheet">
<style>
:root{
  --blue:#1a9be8;
  --ink:#222;
  --grey-text:#666;
  --card-bg:#f3f3f3;
  --card-head:#2b2b2b;
  --bar:#545454;
  --news-bg:#ececec;
  --footer:#404040;
  --rule:#8a8a8a;
  --red:#c0392b;
  --white:#fff;
}
*{box-sizing:border-box;margin:0;padding:0}
html,body{width:750px;height:1200px;overflow:hidden}
body{position:relative;background:var(--white);font-family:Arial,Helvetica,sans-serif;color:var(--ink)}
.abs{position:absolute}

.city-bar{left:0;top:0;width:750px;height:21px;background:var(--blue);color:var(--white);font-size:8px;font-weight:600;padding:5px 0 0 64px;font-family:"Open Sans",sans-serif}
.site-header{left:0;top:21px;width:750px;height:61px;background:var(--white)}
.brand{left:63px;top:13px;display:flex;align-items:center;gap:6px}
.brand-dot{width:20px;height:20px;border-radius:50%;background:var(--blue)}
.brand-name{font-family:"Ubuntu",sans-serif;font-weight:500;font-size:19px;color:var(--blue)}
.main-nav a{position:absolute;top:30px;font-family:"Open Sans",sans-serif;font-weight:600;font-size:10px;color:var(--ink);text-decoration:none;white-space:nowrap}
.main-nav .active::after{content:"";position:absolute;left:-4px;right:-4px;top:18px;height:3px;background:var(--blue)}

.hero{left:0;top:82px;width:750px;height:308px;
  background:
    radial-gradient(ellipse 70px 110px at 345px 170px,rgba(246,214,60,.95),rgba(246,214,60,0) 100%),
    radial-gradient(ellipse 60px 90px at 400px 150px,rgba(240,220,110,.8),rgba(240,220,110,0) 100%),
    radial-gradient(ellipse 60px 70px at 610px 260px,rgba(240,120,150,.7),rgba(240,120,150,0) 100%),
    radial-gradient(ellipse 55px 80px at 710px 250px,rgba(110,200,210,.75),rgba(110,200,210,0) 100%),
    radial-gradient(ellipse 80px 120px at 520px 150px,rgba(70,110,160,.55),rgba(70,110,160,0) 100%),
    linear-gradient(100deg,#4a3526 0%,#7a5a3e 20%,#c59a5c 42%,#d4b27a 55%,#9a7a66 75%,#6a5a54 100%)}
.search-panel{left:72px;top:108px;width:206px;height:264px;background:rgba(26,155,232,.88);color:var(--white);font-size:7px}
.search-panel .title{position:absolute;left:14px;top:16px;font-size:8px;font-family:"Open Sans",sans-serif}
.search-panel .title span{color:#0b2a44}
.format-box{position:absolute;left:18px;top:34px;width:171px;height:44px;background:rgba(255,255,255,.25);border-radius:5px;font-size:7px}
.format-box label{position:absolute;display:flex;align-items:center;gap:5px}
.format-box i{display:inline-block;width:7px;height:7px;background:var(--white)}
.field-label{position:absolute;left:17px;font-size:6.5px}
.field{position:absolute;left:17px;width:169px;height:18px;background:var(--white);border:1px solid #555;color:#333;font-size:7px;padding:4px 6px}
.field.select::after{content:"▾";position:absolute;right:5px;top:3px;font-size:8px}
.field.input{color:#999;font-size:8px;height:19px}

.section-banner{left:269px;top:406px;width:224px;height:31px}
.section-banner span{position:absolute;left:0;top:0;width:224px;height:31px;display:flex;align-items:center;justify-content:center;font-family:"Ubuntu",sans-serif;font-weight:700;font-size:17px;color:var(--white)}

.project-card{width:146px;height:148px;background:var(--card-bg)}
.project-card .head{height:23px;background:var(--card-head);color:var(--white);font-family:"Open Sans",sans-serif;font-weight:600;font-size:9px;display:flex;align-items:center;padding-left:20px}
.project-card.blue .head{background:var(--blue)}
.project-card .photo{position:absolute;left:7px;top:36px;width:133px;height:76px}
.p1{background:
  radial-gradient(ellipse 30px 40px at 25px 45px,rgba(240,200,120,.55),rgba(240,200,120,0)),
  radial-gradient(ellipse 30px 35px at 105px 50px,rgba(240,200,120,.45),rgba(240,200,120,0)),
  linear-gradient(90deg,#4a3a30 0%,#6b5646 30%,#9aa8b8 48%,#6b5646 66%,#4a3a30 100%)}
.p2{background:
  radial-gradient(ellipse 55px 35px at 70px 40px,rgba(245,245,245,.95),rgba(245,245,245,0)),
  linear-gradient(180deg,#4d7fc4 0%,#9fb8d8 30%,#dde3e8 55%,#7d8e78 100%)}
.p3{background:
  radial-gradient(ellipse 50px 25px at 80px 35px,rgba(150,50,40,.85),rgba(150,50,40,0)),
  linear-gradient(180deg,#6c5a86 0%,#a2757a 35%,#6a3a30 60%,#2a5f88 100%)}
.project-card .more{position:absolute;left:5px;top:120px;width:135px;height:18px;background:var(--bar);color:var(--white);font-size:8.5px;display:flex;align-items:center;justify-content:space-between;padding:0 10px 0 8px}

.news{left:0;top:808px;width:750px;height:156px;background:var(--news-bg)}
.news h2{position:absolute;left:63px;top:17px;font-size:14px;color:var(--blue);font-weight:700;letter-spacing:.3px}
.news-item{width:300px}
.news-item .num{position:absolute;left:0;top:8px;font-size:13.5px;color:var(--red);border-bottom:1px solid var(--red);line-height:14px}
.news-item h3{position:absolute;left:30px;top:0;font-size:9px;font-weight:400;line-height:10.5px;color:var(--ink);white-space:nowrap}
.news-item p{position:absolute;left:32px;top:28px;width:258px;font-size:7.6px;line-height:11.2px;color:var(--grey-text)}
.news-item .read{position:absolute;left:32px;top:66px;font-size:7.6px;font-weight:700;color:var(--ink)}
.news .rule{left:381px;top:44px;width:1px;height:104px;background:#ccc}

.site-footer{left:0;top:964px;width:750px;height:178px;background:var(--footer);color:var(--white)}
.site-footer h4{position:absolute;font-family:"Ubuntu",sans-serif;font-weight:500;font-size:13.5px}
.site-footer .rule{position:absolute;top:10px;width:1px;height:160px;background:var(--rule)}
.site-footer .copy{position:absolute;font-size:8px;line-height:11px}
.field-light{position:absolute;background:var(--white);color:#999;font-size:7.5px;padding:4px 5px}
.btn{position:absolute;width:64px;height:23px;background:var(--blue);border:1px solid #7fd0ff;color:var(--white);font-family:"Ubuntu",sans-serif;font-weight:700;font-size:11px;display:flex;align-items:center;justify-content:center;border-radius:2px}

.bottom-bar{left:0;top:1142px;width:750px;height:58px;background:var(--blue);color:var(--white)}
.bottom-bar .legal{position:absolute;left:59px;top:20px;font-size:8px;line-height:16px}
.bottom-bar .brand{left:526px;top:14px}
.bottom-bar .brand-dot{background:var(--white)}
.bottom-bar .brand-name{color:var(--white)}
</style>
</head>
<body>

<div class="abs city-bar">Bangalore | Chennai | Greater Noida | Gurgaon | Hyderabad | Jaipur | Khanna | Kolkatta | Mumbai | Noida | Pune | Surat</div>

<header class="abs site-header">
  <div class="abs brand"><span class="brand-dot"></span><span class="brand-name">lotstallmart</span></div>
  <nav class="abs main-nav">
    <a class="active" style="left:386px">Home</a>
    <a style="left:439px">Advertise with us</a>
    <a style="left:543px">Mart Wizards</a>
    <a style="left:625px">Listing Alert</a>
  </nav>
</header>

<div class="abs hero" role="img" aria-label="Photo of a smiling family shopping in a store with yellow sale signs"></div>

<form class="abs search-panel">
  <div class="title">Select Retail Format: <span>Meaning of Retail Format</span></div>
  <div class="format-box">
    <label style="left:9px;top:9px"><i></i>Retail Malls</label>
    <label style="left:79px;top:9px"><i></i>Shopping Complex</label>
    <label style="left:9px;top:27px"><i></i>High Street Sh</label>
    <label style="left:79px;top:27px"><i></i>Retail Warehouses</label>
  </div>
  <div class="field-label" style="top:89px">Sale Or Rent Or Both:</div>
  <div class="field select" style="top:98px">Both</div>
  <div class="field-label" style="top:126px">Select City-</div>
  <div class="field select" style="top:133px">--Select--</div>
  <div class="field-label" style="top:160px">Select Locality/Micro-Market</div>
  <div class="field select" style="top:168px">--Select--</div>
  <div class="field-label" style="top:195px">Enter Keywords:</div>
  <div class="field input" style="top:202px">Name of Project, Developer etc</div>
</form>

<div class="abs section-banner">
  <svg width="224" height="31" viewBox="0 0 224 31"><polygon points="10,0 214,0 224,15.5 214,31 10,31 0,15.5" fill="#1a9be8"/></svg>
  <span>CURRENT PROJECTS</span>
</div>

<div class="abs project-card" style="left:60px;top:458px"><div class="head">LOREM IPSUM DOLOR</div><div class="photo p1" role="img" aria-label="Apartment building at dusk"></div><div class="more"><svg width="12" height="12" viewBox="0 0 12 12"><path d="M6 1a3.5 3.5 0 0 1 3.5 3.5C9.5 7 6 11 6 11S2.5 7 2.5 4.5A3.5 3.5 0 0 1 6 1z" fill="#1a9be8"/><circle cx="6" cy="4.5" r="1.3" fill="#fff"/></svg><span>Readmore ›</span></div></div>
<div class="abs project-card" style="left:221px;top:458px"><div class="head">LOREM IPSUM DOLOR</div><div class="photo p2" role="img" aria-label="White residential block"></div><div class="more"><svg width="12" height="12" viewBox="0 0 12 12"><path d="M6 1a3.5 3.5 0 0 1 3.5 3.5C9.5 7 6 11 6 11S2.5 7 2.5 4.5A3.5 3.5 0 0 1 6 1z" fill="#1a9be8"/><circle cx="6" cy="4.5" r="1.3" fill="#fff"/></svg><span>Readmore ›</span></div></div>
<div class="abs project-card" style="left:382px;top:458px"><div class="head">LOREM IPSUM DOLOR</div><div class="photo p3" role="img" aria-label="Modern villa with pool"></div><div class="more"><svg width="12" height="12" viewBox="0 0 12 12"><path d="M6 1a3.5 3.5 0 0 1 3.5 3.5C9.5 7 6 11 6 11S2.5 7 2.5 4.5A3.5 3.5 0 0 1 6 1z" fill="#1a9be8"/><circle cx="6" cy="4.5" r="1.3" fill="#fff"/></svg><span>Readmore ›</span></div></div>
<div class="abs project-card" style="left:539px;top:457px"><div class="head">LOREM IPSUM DOLOR</div><div class="photo p1" role="img" aria-label="Apartment building at dusk"></div><div class="more"><svg width="12" height="12" viewBox="0 0 12 12"><path d="M6 1a3.5 3.5 0 0 1 3.5 3.5C9.5 7 6 11 6 11S2.5 7 2.5 4.5A3.5 3.5 0 0 1 6 1z" fill="#1a9be8"/><circle cx="6" cy="4.5" r="1.3" fill="#fff"/></svg><span>Readmore ›</span></div></div>

<div class="abs project-card blue" style="left:60px;top:625px"><div class="head">LOREM IPSUM DOLOR</div><div class="photo p1" role="img" aria-label="Apartment building at dusk"></div><div class="more"><svg width="12" height="12" viewBox="0 0 12 12"><path d="M6 1a3.5 3.5 0 0 1 3.5 3.5C9.5 7 6 11 6 11S2.5 7 2.5 4.5A3.5 3.5 0 0 1 6 1z" fill="#1a9be8"/><circle cx="6" cy="4.5" r="1.3" fill="#fff"/></svg><span>Readmore ›</span></div></div>
<div class="abs project-card blue" style="left:221px;top:625px"><div class="head">LOREM IPSUM DOLOR</div><div class="photo p2" role="img" aria-label="White residential block"></div><div class="more"><svg width="12" height="12" viewBox="0 0 12 12"><path d="M6 1a3.5 3.5 0 0 1 3.5 3.5C9.5 7 6 11 6 11S2.5 7 2.5 4.5A3.5 3.5 0 0 1 6 1z" fill="#1a9be8"/><circle cx="6" cy="4.5" r="1.3" fill="#fff"/></svg><span>Readmore ›</span></div></div>
<div class="abs project-card blue" style="left:382px;top:625px"><div class="head">LOREM IPSUM DOLOR</div><div class="photo p3" role="img" aria-label="Modern villa with pool"></div><div class="more"><svg width="12" height="12" viewBox="0 0 12 12"><path d="M6 1a3.5 3.5 0 0 1 3.5 3.5C9.5 7 6 11 6 11S2.5 7 2.5 4.5A3.5 3.5 0 0 1 6 1z" fill="#1a9be8"/><circle cx="6" cy="4.5" r="1.3" fill="#fff"/></svg><span>Readmore ›</span></div></div>
<div class="abs project-card blue" style="left:539px;top:624px"><div class="head">LOREM IPSUM DOLOR</div><div class="photo p1" role="img" aria-label="Apartment building at dusk"></div><div class="more"><svg width="12" height="12" viewBox="0 0 12 12"><path d="M6 1a3.5 3.5 0 0 1 3.5 3.5C9.5 7 6 11 6 11S2.5 7 2.5 4.5A3.5 3.5 0 0 1 6 1z" fill="#1a9be8"/><circle cx="6" cy="4.5" r="1.3" fill="#fff"/></svg><span>Readmore ›</span></div></div>

<section class="abs news">
  <h2>CORPORATE NEWS</h2>
  <article class="abs news-item" style="left:69px;top:49px">
    <span class="num">01</span>
    <h3>LOREM IPSUM DOLOR SIT AMET<br>CONSECTETUR ADIPISICING</h3>
    <p>Sorrupti quos dolores etquas molestias exceptur sint occaecati cupificia deserunt mollitia animi id est laborum et dolorum fuga. Et harum quidem rerum facilisest et expedita distinctio.Sorrupti quos dolores etquas moles</p>
    <span class="read">read more...</span>
  </article>
  <div class="abs rule"></div>
  <article class="abs news-item" style="left:404px;top:47px">
    <span class="num">02</span>
    <h3>LOREM IPSUM DOLOR SIT AMET<br>CONSECTETUR ADIPISICING</h3>
    <p>Sorrupti quos dolores etquas molestias exceptur sint occaecati cupificia deserunt mollitia animi id est laborum et dolorum fuga. Et harum quidem rerum facilisest et expedita distinctio.Sorrupti quos dolores etquas moles</p>
    <span class="read">read more...</span>
  </article>
</section>

<footer class="abs site-footer">
  <h4 style="left:63px;top:20px">Listing Alert</h4>
  <svg class="abs" style="left:62px;top:38px" width="38" height="36" viewBox="0 0 38 36"><polygon points="19,0 38,14 38,36 0,36 0,14" fill="#2f7fc4"/><rect x="5" y="6" width="28" height="22" fill="#f2f2f2"/><polygon points="0,14 19,27 38,14 38,36 0,36" fill="#d8d8d8"/><text x="19" y="20" font-size="12" text-anchor="middle" fill="#444" font-family="Arial">@</text></svg>
  <div class="copy" style="left:108px;top:45px">Suscribe for Fortnightly Email<br>update on New Listings @<br>lotstallmart</div>
  <div class="field-light" style="left:63px;top:86px;width:151px;height:20px">Email Your Email Address:</div>
  <div class="btn" style="left:150px;top:118px">Subscribe</div>
  <div class="rule" style="left:230px"></div>

  <h4 style="left:249px;top:20px">Editor's Choice</h4>
  <div class="copy" style="left:249px;top:44px;width:214px;line-height:12.5px">A "Select" Listing of Retail Properties Handpicked by our Editors based on their own positive evaluation on parameters &amp; attributes such as Design Concept, Location, Developer, Success Potential. So Read On to Check Out for yourself ............</div>
  <div class="rule" style="left:481px"></div>

  <h4 style="left:518px;top:20px">Mart Wizards</h4>
  <div class="field-light" style="left:518px;top:44px;width:164px;height:18px">Email Your Email Address:</div>
  <div class="field-light" style="left:518px;top:74px;width:164px;height:35px">Add Description of Requirement</div>
  <div class="btn" style="left:618px;top:118px;font-size:12px">Send</div>
</footer>

<div class="abs bottom-bar">
  <div class="legal">Copyright © 2013 Bharat Retail Hub.com. All rights reserved.<br>website by Nexora Webworks.</div>
  <div class="abs brand"><span class="brand-dot"></span><span class="brand-name">lotstallmart</span></div>
</div>

</body>
</html>
```